Equine Podcast Cover Art Design

We need catchy cover art for a horse related podcast "Ride Onward Together"
Brief show description"
Whether you want to ride to experience horses, develop yourself to the next level as a horseman/horsewoman or ride to improve your physical and mental health, we are committed to helping you Ride Onward TogetherĀ®. Join us as we explore the nuance of equine management and sports as well as interview industry professionals to provide you with the knowledge necessary to be a better partner for your equine friends.
I have uploaded two existing logos we use for various purposes to give you an idea of existing style.
Target Market(s)
Horse owners and other equine professionals
Look and feel
Each slider illustrates characteristics of the customer's brand and the style your logo design should communicate.

```html
<!DOCTYPE html>
<html lang="en">
<head>
<meta charset="utf-8">
<title>Ride Onward Together® Podcast Cover</title>
<link rel="stylesheet" href="https://fonts.googleapis.com/css2?family=Bebas+Neue&family=Antonio:wght@200&family=Josefin+Sans:wght@300;400&display=swap">
<style>
  :root {
    --night: #040404;
    --saddle: #7d4f3f;
    --ember-1: #ff7a00;
    --ember-2: #ffb400;
    --ember-3: #fff200;
    --sand: #f2bd82;
    --white: #ffffff;
    --coat-deep: #2a140b;
    --coat-mid: #6b3518;
    --coat-light: #a45a2c;
  }
  * { margin: 0; padding: 0; box-sizing: border-box; }
  html, body { width: 1200px; height: 1200px; overflow: hidden; background: var(--night); }
  .cover {
    position: relative;
    width: 1200px;
    height: 1200px;
    background: var(--night);
    overflow: hidden;
  }
  .cover__portrait {
    position: absolute;
    left: 560px;
    top: 0;
    width: 640px;
    height: 1200px;
    background:
      radial-gradient(ellipse 45% 36% at 55% 46%, var(--coat-light) 0%, var(--coat-mid) 45%, transparent 80%),
      radial-gradient(ellipse 55% 45% at 70% 82%, var(--coat-mid) 0%, var(--coat-deep) 55%, transparent 90%),
      linear-gradient(90deg, transparent 0%, var(--coat-deep) 35%, var(--coat-deep) 100%);
  }
  .brand {
    position: absolute;
    left: 97px;
    top: 72px;
    width: 184px;
    height: 184px;
    border: 3px solid var(--white);
    border-radius: 50%;
    display: flex;
    flex-direction: column;
    align-items: center;
    justify-content: center;
    color: var(--white);
    font-family: "Bebas Neue", sans-serif;
    font-size: 26px;
    line-height: 1;
    letter-spacing: 1px;
    text-align: center;
  }
  .brand__place { font-size: 14px; letter-spacing: 2px; margin-top: 6px; }
  .title__lead {
    position: absolute;
    left: 83px;
    top: 276px;
    font-family: "Bebas Neue", sans-serif;
    font-weight: 400;
    color: var(--saddle);
    font-size: 200px;
    line-height: 162px;
    letter-spacing: -1px;
  }
  .title__lead span { display: block; height: 162px; }
  .title__main {
    position: absolute;
    left: 66px;
    top: 639px;
    font-family: "Antonio", sans-serif;
    font-weight: 200;
    font-size: 351px;
    line-height: 1;
    transform: scaleX(0.55);
    transform-origin: left top;
    background: linear-gradient(180deg, var(--ember-1) 0%, var(--ember-2) 50%, var(--ember-3) 62%, var(--ember-1) 100%);
    -webkit-background-clip: text;
    background-clip: text;
    color: transparent;
    white-space: nowrap;
  }
  .title__mark {
    position: absolute;
    left: 668px;
    top: 724px;
    width: 54px;
    height: 54px;
    border: 5px solid var(--ember-1);
    border-radius: 50%;
    display: flex;
    align-items: center;
    justify-content: center;
    font-family: "Josefin Sans", sans-serif;
    font-weight: 400;
    font-size: 30px;
    line-height: 1;
    padding-top: 4px;
    color: var(--ember-1);
  }
  .tagline {
    position: absolute;
    left: 76px;
    top: 1076px;
    font-family: "Josefin Sans", sans-serif;
    font-weight: 300;
    font-size: 36px;
    letter-spacing: 9px;
    color: var(--sand);
  }
</style>
</head>
<body>
  <main class="cover">
    <div class="cover__portrait" role="img" aria-label="Portrait of a bay horse with flowing dark mane against a black background"></div>

    <div class="brand">
      <span class="brand__name">Willow Bend<br>Farm</span>
      <span class="brand__place">Ashford, Vermont</span>
    </div>

    <h1 class="title">
      <span class="title__lead"><span>RIDE</span><span>ONWARD</span></span>
      <span class="title__main">TOGETHER</span>
    </h1>
    <span class="title__mark" aria-label="registered">R</span>

    <p class="tagline">PODCAST</p>
  </main>
</body>
</html>
```